Professional violinist needs business cards

I am trying to attract the following jobs:
-private violin lessons (primarily classical)
-performance gigs (weddings, birthday parties, funerals, etc.)
-collaborations with other artists (studio recordings, performances)

I want to communicate that I have a very high standard of excellence for my work, but I also love people and celebrations.
Values/style words I like are:
love, joy, peace, fun, beauty, authenticity, excellence, warmth, refined/sleek, free spirited. If that's too confusing, just ignore :)

I will attach my favorite business card template that I could find on Canva. The lines are supposed to be like a music staff, which I think is really cool, but I also don't want it to look too busy. I like the simple black and white--I think it looks sharp--but I also am open to other ideas. I also have seen business cards with pictures included that looked great, so I attached an image that could be used as well.

I am also attaching a file that I made of my initials that could be used as a logo, but I'm not sure if it should be included.

Information on the card:
-My name (18 letters total)
-"violinist"
-phone number, email, website

Thank you!

```html
<!DOCTYPE html>
<html lang="en">
<head>
<meta charset="utf-8">
<title>Lena Marlow – Violinist Business Cards</title>
<link href="https://fonts.googleapis.com/css2?family=Montserrat:wght@400;500;600&family=Roboto:wght@400&display=swap" rel="stylesheet">
<style>
  :root {
    --backdrop: #2a2a2c;
    --card-black: #050505;
    --card-sheen: #1c1c1d;
    --gold: #d19e3c;
    --gold-soft: #b88a33;
    --white: #f2f2f2;
    --grey-line: #8a8a8a;
    --photo-dark: #0b0908;
    --photo-warm: #4a2e22;
  }
  * { box-sizing: border-box; margin: 0; padding: 0; }
  html, body { width: 1200px; height: 900px; overflow: hidden; }
  body {
    background: var(--backdrop);
    position: relative;
    font-family: "Roboto", Arial, sans-serif;
  }
  .card {
    position: absolute;
    left: 220px;
    width: 760px;
    height: 380px;
    overflow: hidden;
    background: linear-gradient(100deg, var(--card-black) 0%, var(--card-black) 55%, var(--card-sheen) 100%);
    box-shadow: 0 14px 30px rgba(0,0,0,0.55);
  }
  .card--front { top: 45px; }
  .card--back { top: 475px; }

  /* Front */
  .staff {
    position: absolute;
    inset: 0;
  }
  .staff__line {
    position: absolute;
    left: 0;
    right: 0;
    height: 4px;
    background: var(--gold);
  }
  .brand-name {
    position: absolute;
    left: 40px;
    top: 138px;
    font-family: "Montserrat", Arial, sans-serif;
    font-weight: 600;
    font-size: 86px;
    line-height: 1;
    letter-spacing: -1px;
    color: var(--gold);
    background: var(--card-black);
    padding: 6px 18px 10px;
  }
  .front-website {
    position: absolute;
    right: 36px;
    bottom: 26px;
    font-family: "Montserrat", Arial, sans-serif;
    font-size: 15px;
    letter-spacing: 1px;
    color: var(--white);
  }

  /* Back */
  .portrait {
    position: absolute;
    left: 28px;
    top: 0;
    width: 250px;
    height: 380px;
    background: radial-gradient(ellipse at 50% 45%, var(--photo-warm) 0%, var(--photo-dark) 70%);
  }
  .identity {
    position: absolute;
    left: 300px;
    top: 118px;
    right: 30px;
  }
  .identity__row {
    display: flex;
    align-items: flex-end;
    gap: 14px;
  }
  .identity__name {
    font-family: "Montserrat", Arial, sans-serif;
    font-weight: 500;
    font-size: 28px;
    color: var(--gold);
    white-space: nowrap;
    line-height: 1;
  }
  .identity__rule {
    flex: 1;
    height: 2px;
    background: var(--gold-soft);
    margin-bottom: 6px;
  }
  .identity__role {
    font-family: "Montserrat", Arial, sans-serif;
    font-size: 14px;
    color: var(--white);
    white-space: nowrap;
    line-height: 1;
  }
  .identity__rule--grey { background: var(--grey-line); height: 1px; margin-bottom: 5px; }
  .identity__row + .identity__row { margin-top: 8px; }

  .contact-list {
    position: absolute;
    left: 320px;
    right: 30px;
    top: 230px;
    list-style: none;
  }
  .contact-list__item {
    display: flex;
    align-items: center;
    gap: 14px;
    height: 34px;
    border-bottom: 1px solid var(--grey-line);
    font-size: 17px;
    color: var(--white);
  }
  .contact-list__icon { width: 18px; height: 18px; flex: none; }
</style>
</head>
<body>

  <section class="card card--front" aria-label="Card front">
    <div class="staff">
      <span class="staff__line" style="top:48px"></span>
      <span class="staff__line" style="top:108px"></span>
      <span class="staff__line" style="top:168px"></span>
      <span class="staff__line" style="top:228px"></span>
      <span class="staff__line" style="top:288px"></span>
      <span class="staff__line" style="top:348px"></span>
    </div>
    <div class="brand-name">Lena Marlow</div>
    <div class="front-website">www.yourwebsite.com</div>
  </section>

  <section class="card card--back" aria-label="Card back">
    <div class="portrait" role="img" aria-label="Photo of the violinist in a black dress holding her violin and bow"></div>

    <div class="identity">
      <div class="identity__row">
        <span class="identity__name">Lena Marlow</span>
        <span class="identity__rule"></span>
      </div>
      <div class="identity__row">
        <span class="identity__role">Violinist</span>
        <span class="identity__rule identity__rule--grey"></span>
      </div>
    </div>

    <ul class="contact-list">
      <li class="contact-list__item">
        <svg class="contact-list__icon" viewBox="0 0 20 20" aria-hidden="true">
          <path d="M2 7 Q10 1 18 7 L16 9 L13 7 L13 5 Q10 4 7 5 L7 7 L4 9 Z" fill="var(--gold)"/>
          <rect x="5" y="10" width="10" height="7" rx="1" fill="var(--gold)"/>
        </svg>
        <span>012 3456 7890</span>
      </li>
      <li class="contact-list__item">
        <svg class="contact-list__icon" viewBox="0 0 20 20" aria-hidden="true">
          <rect x="2" y="5" width="16" height="11" fill="none" stroke="var(--gold)" stroke-width="2"/>
          <path d="M2 5 L10 11 L18 5" fill="none" stroke="var(--gold)" stroke-width="2"/>
        </svg>
        <span>info@yourwebsite.com</span>
      </li>
      <li class="contact-list__item">
        <svg class="contact-list__icon" viewBox="0 0 20 20" aria-hidden="true">
          <circle cx="10" cy="10" r="8" fill="none" stroke="var(--gold)" stroke-width="2"/>
          <ellipse cx="10" cy="10" rx="3.5" ry="8" fill="none" stroke="var(--gold)" stroke-width="1.5"/>
          <line x1="2" y1="10" x2="18" y2="10" stroke="var(--gold)" stroke-width="1.5"/>
        </svg>
        <span>www.yourwebsite.com</span>
      </li>
    </ul>
  </section>

</body>
</html>
```